Stationery Design Project for Nimbora, Chicago

Nimbora, a street parking application which helps car drivers find a street parking spot by offering an ideal path along which to look for parking. This path is calculated by our algorithm based on data (e.g. historical data, baseball games schedule, etc.). Along this path the driver will find a spot and will also save 70% of the search time. Customer we target is reg. between 21 and 45 yo.

We envision something young, fresh, bright and original. Slightly abstract maybe. It should represent the idea and elements of finding street parking in the city, e.g. car(s), parking spot, people, city, etc. (just ideas!).

Logo is attached.

Requirement:
- Business Cards (2 Sided Full Color CMYK)
- Letterhead (1 Sided Full Color CMYK)
- Envelope (1 Sided Full Color CMYK)
- Sticker (1 Sided Full Color CMYK), round with a 2inch diameter.

Reason: We're starting to get more and more designs and need more time to look into all of them. Very exciting!! Thanks to everybody!

Hi all, we're in the process of selecting our favs. Though choices!!! Really good submissions. Will keep you posted and sorry for the delay.

Target Market(s)

Car drivers and owners between 21 and 45

Industry/Entity Type

Parking

Requirements
Must have
• Sticker should be round and include company URL nimbora.com and the new logo which we will attach soon.
Should not have
• Should not be too serious or boring.

```html
<!DOCTYPE html>
<html lang="en">
<head>
<meta charset="utf-8">
<title>Nimbora business card</title>
<link rel="stylesheet" href="https://fonts.googleapis.com/css2?family=Open+Sans:wght@400;600;700&display=swap">
<style>
  :root {
    --backdrop: #ecebe8;
    --card: #ffffff;
    --card-edge: #8a8a8a;
    --brand-blue: #1f63c9;
    --name-blue: #2b86c5;
    --ink: #2f2f2f;
    --ink-soft: #3c3c3c;
    --divider: #9a9a9a;
  }
  * { margin: 0; padding: 0; box-sizing: border-box; }
  html, body {
    width: 1200px; height: 403px; overflow: hidden;
    background: var(--backdrop);
    font-family: "Open Sans", Arial, sans-serif;
  }
  .stage { position: relative; width: 1200px; height: 403px; }
  .card {
    position: absolute; top: 54px;
    width: 506px; height: 288px;
    background: var(--card);
    border: 1px solid var(--card-edge);
  }
  .card--front { left: 64px; }
  .card--back { left: 617px; }

  .brand-dot {
    position: absolute; border-radius: 50%;
    background: var(--brand-blue);
  }
  .brand-name {
    position: absolute; color: var(--ink);
    font-weight: 600; line-height: 1; letter-spacing: 0.5px;
  }

  .card--front .brand-dot { left: 29px; top: 118px; width: 66px; height: 66px; }
  .card--front .brand-name { left: 106px; top: 133px; font-size: 36px; }

  .divider {
    position: absolute; left: 305px; top: 67px;
    width: 1px; height: 170px; background: var(--divider);
  }
  .details { position: absolute; left: 325px; top: 62px; color: var(--ink-soft); }
  .holder { font-size: 19px; font-weight: 700; color: var(--name-blue); line-height: 1.2; }
  .holder .title { font-size: 15px; font-weight: 400; }
  .address { margin-top: 17px; font-size: 13px; line-height: 18px; }
  .contacts { list-style: none; margin-top: 15px; font-size: 13px; line-height: 18.5px; }
  .contacts li { display: flex; align-items: center; gap: 7px; }
  .contacts svg { width: 10px; height: 10px; fill: var(--ink-soft); flex: none; }

  .card--back .brand-dot { left: 97px; top: 91px; width: 88px; height: 88px; }
  .card--back .brand-name { left: 198px; top: 105px; font-size: 52px; }
  .card--back .web {
    position: absolute; left: 0; right: 0; top: 220px;
    text-align: center; font-size: 16px; letter-spacing: 2px; color: var(--ink);
  }
</style>
</head>
<body>
<main class="stage">
  <section class="card card--front" aria-label="Business card front">
    <span class="brand-dot" aria-hidden="true"></span>
    <span class="brand-name">nimbora</span>
    <span class="divider" aria-hidden="true"></span>
    <div class="details">
      <p class="holder">Your Name , <span class="title">Title</span></p>
      <p class="address">Complex Name, Street Name<br>Area, City Name,000 000</p>
      <ul class="contacts">
        <li><svg viewBox="0 0 10 10"><path d="M2 0.5l1.8 2.2-1 1.1c.6 1.3 1.5 2.2 2.7 2.8l1.1-1L9 7.5 7.8 9.3C4 9 1 6 .7 2.1z"/></svg>+1 312 555 0147</li>
        <li><svg viewBox="0 0 10 10"><path d="M2.5 0h5v10h-5zM3.5 1v6h3V1zM4.5 8h1v1h-1z" fill-rule="evenodd"/></svg>+1 312 555 0147</li>
        <li><svg viewBox="0 0 10 10"><path d="M0 2h10v6.5H0zM1 3l4 3 4-3V2.8L5 5.3 1 2.8z" fill-rule="evenodd"/></svg>info@nimbora.com</li>
        <li><svg viewBox="0 0 10 10"><circle cx="5" cy="5" r="4.6"/><path d="M0.5 5h9M5 0.5v9" stroke="#fff" stroke-width="0.8"/></svg>www.nimbora.com</li>
      </ul>
    </div>
  </section>

  <section class="card card--back" aria-label="Business card back">
    <span class="brand-dot" aria-hidden="true"></span>
    <span class="brand-name">nimbora</span>
    <p class="web">www.nimbora.com</p>
  </section>
</main>
</body>
</html>
```